RW Framewell Inc Business cards

We need business cards using our existing logo but slightly modified. Right now the logo says RW Loadbearing Masonry. We want to keep the RW part of the design, but replace the Structural Concrete portion with "FRAMEWELL". Please see the attached file.
Ideally this would be a blank template so we can add Different Names, titles, and phone numbers later.
On the one side we want only the logo and on the other side the detail. I'm attaching an example for you to see.
Please reach out with any other questions. Our address and other details will be given out once we find a design we like.

Target Market(s)

Construction Industry

```html
<!DOCTYPE html>
<html lang="en">
<head>
<meta charset="utf-8">
<title>RW Framewell Inc – Business Cards</title>
<link href="https://fonts.googleapis.com/css2?family=Arimo:wght@400;700&display=swap" rel="stylesheet">
<style>
  :root {
    --page-bg: #e6e7e9;
    --brand-blue: #0077c8;
    --band-blue: #0a6cb8;
    --rule-grey: #7a7c80;
    --ink: #2b2b2d;
    --paper: #f3f3f3;
    --white: #ffffff;
  }
  * { box-sizing: border-box; margin: 0; padding: 0; }
  html, body {
    width: 1200px; height: 900px; overflow: hidden;
    background: var(--page-bg);
    font-family: "Arimo", Arial, sans-serif;
  }
  .sheet {
    width: 1200px; height: 900px;
    display: flex; flex-direction: column; align-items: center; justify-content: center;
    gap: 40px;
  }
  .card {
    position: relative;
    width: 700px; height: 400px;
    overflow: hidden;
    box-shadow: 0 6px 18px rgba(0,0,0,.12);
  }

  /* Logo side */
  .card--logo {
    background: var(--brand-blue);
    display: flex; align-items: center; justify-content: center;
  }
  .wordmark {
    display: flex; flex-direction: column; align-items: center;
    font-weight: 700; color: var(--white); line-height: 1;
  }
  .wordmark__initials { font-size: 96px; letter-spacing: 4px; }
  .wordmark__name { font-size: 16px; letter-spacing: 12px; margin-top: 12px; margin-right: -12px; }

  /* Detail side */
  .card--details { background: var(--paper); }
  .card--details .wordmark {
    position: absolute; top: 62px; right: 35px;
    color: var(--brand-blue); align-items: flex-end;
  }
  .card--details .wordmark__initials { font-size: 82px; letter-spacing: 2px; }
  .card--details .wordmark__name { font-size: 14px; letter-spacing: 11.6px; margin-top: 8px; margin-right: -11px; }

  .person { position: absolute; left: 33px; top: 210px; right: 35px; }
  .person__name {
    font-size: 25px; font-weight: 700; color: var(--brand-blue);
    letter-spacing: .3px;
  }
  .person__title-row { display: flex; align-items: center; gap: 9px; margin-top: 6px; }
  .person__title { font-size: 16px; color: var(--ink); white-space: nowrap; }
  .person__rule { flex: 1; height: 1px; background: var(--rule-grey); }

  .contact { position: absolute; left: 33px; top: 285px; list-style: none; }
  .contact__item {
    display: flex; align-items: center; gap: 7px;
    font-size: 16px; color: var(--ink); height: 23px;
  }
  .contact__icon { width: 12px; height: 12px; fill: var(--brand-blue); flex: none; }

  .address {
    position: absolute; right: 35px; top: 311px;
    font-style: normal; text-align: right;
    font-size: 16px; line-height: 21px; color: var(--ink);
  }
  .band { position: absolute; left: 0; bottom: 0; width: 700px; height: 32px; }
</style>
</head>
<body>
<main class="sheet">

  <section class="card card--logo" aria-label="Business card, logo side">
    <div class="wordmark">
      <span class="wordmark__initials">RW</span>
      <span class="wordmark__name">FRAMEWELL</span>
    </div>
  </section>

  <section class="card card--details" aria-label="Business card, detail side">
    <div class="wordmark">
      <span class="wordmark__initials">RW</span>
      <span class="wordmark__name">FRAMEWELL</span>
    </div>

    <div class="person">
      <h1 class="person__name">DALEN MARSH</h1>
      <div class="person__title-row">
        <span class="person__title">Owner/CEO</span>
        <span class="person__rule"></span>
      </div>
    </div>

    <ul class="contact">
      <li class="contact__item">
        <svg class="contact__icon" viewBox="0 0 12 12" aria-hidden="true"><path d="M2.4 0.6 4.3 2.5 3.2 4a7 7 0 0 0 4.8 4.8l1.5-1.1 1.9 1.9-1.3 1.7C5 11 1 7 .6 2z"/></svg>
        555-310-8842
      </li>
      <li class="contact__item">
        <svg class="contact__icon" viewBox="0 0 12 12" aria-hidden="true"><path d="M0 2h12v8H0z M0.8 2.6 6 6.6l5.2-4" stroke="#f3f3f3" stroke-width=".9"/></svg>
        info@rwframewell.com
      </li>
      <li class="contact__item">
        <svg class="contact__icon" viewBox="0 0 12 12" aria-hidden="true"><circle cx="6" cy="6" r="6"/><path d="M3 3.5c1 .2 1.6 1 1.3 2-.3.8.6 1.2.4 2.2M7.5 1.5c-.4.9.5 1.5 1.4 1.3.8 1 .4 2.3-.4 3" stroke="#f3f3f3" stroke-width=".9" fill="none"/></svg>
        www.rwframewell.com
      </li>
    </ul>

    <address class="address">
      1480 Cedar Ridge Road<br>
      Harlow County 7406
    </address>

    <svg class="band" viewBox="0 0 700 32" preserveAspectRatio="none" aria-hidden="true">
      <rect x="0" y="6" width="420" height="3" fill="var(--rule-grey)"/>
      <path d="M0 14 H395 C420 14 425 3 450 3 H700 V32 H0 Z" fill="var(--band-blue)"/>
    </svg>
  </section>

</main>
</body>
</html>
```